New e-commerce site needs a clean, responsive design with a focus on great UX

Sky Ledger is a start-up online firearm parts store, aimed at offering a great shopping experience. We want to differentiate ourselves from other online stores firstly through a clean design that doesn't try to compete with itself for user attention.

This project is for the home page specifically, but further work may include the individual product page, category page, and checkout flow pages.

The design must:
* Be clean and clutter-free, with judicious use of white space.
* Be responsive, in that elements must be able to reflow without problems, such that mobile users retain full functionality.
* Be content-focussed, with header and footer styling taking a backseat to content styling.
* Avoid column-based side bars (Navigation, etc.) as far as possible.
* Avoid carousels, or any other sort of rotating content. We want to avoid animations of any kind, again, to avoid competing with ourselves for user attention.
* Scroll cleanly. Scrolling is fine - we don't care about cramming everything in above The Fold, so long as scrolling cues are available.
* Feature a clean typographical hierarchy to properly direct user attention.
* A clean grid, such that blocks line up nicely, within reason. We understand that text does not always work out in perfect rectangles.

The current placeholder design is viewable at http://www.skyledger.co.za/ (Also check it out on a mobile device to see responsive behaviour)

Sites in the same type of industry that have the type of clean look we want:
* http://www.trelvonix.com/ (Not ideal, but in the right general direction)
* http://pomrick.dunvelaco.com/ (Great-looking content areas and fantastic responsive design)
The content areas are the main focus here, especially on the latter site. We don't want the same type of header or footer styling as these sites, as exemplified by the very Bootstrappy placeholder site we currently have.

Elements we would like to see in the design:
* The slogan with an AC-130 gunship (The current one is a public domain image), which gives context behind the brand name and ties into the silhouette placeholder logo.
* A product spotlight, to highlight a particular product we would like to bring attention to. It need not be as verbose as the "Introducing the Brass Tidy" spotlight currently on the placeholder site, but should still be a headline spotlight.
* "Mini" spotlights for specific brands, categories, or specific products. This is sort-of implemented as the "Brands In Stock" section on the placeholder site, but the final design would probably have more squarish blocks, so that a specific product consisting of image and headline could be featured. Feel free to use random product images as needed.

Other notes:
* The use of Courier New for headings is to try convey a "military/air force" feel, but we don't want to go overboard with that, which is why there are no other "military" aspects to the site. Exploration of other options are welcome.
* Please let us know if there's any other information or guidance we can provide to help with the design process.

Edit 2015/01/07 07:40 UTC:
* This contest is for PSD designs, but if you prefer to implement it using HTML & CSS, you are welcome to do so, with Bootstrap being preferred. The requirement to keep in mind is that whatever is in the design must be able to reflow cleanly for lower-resolution devices (Down to 320px wide). In other words, the design must be able to be implemented in a responsive manner.
* We don't strictly require the design to include the AC-130 gunship, but it does help tie the brand name to the slogan and thus anchor the brand name in users' minds. If the same message can be conveyed differently, we're happy to consider it.
* We would prefer to avoid stereotypical "military" elements, such as camouflage, etc.

Edit 2015/01/07 08:08 UTC:
* The design must avoid pop-up menus, or anything that would require pop-up menus.
* Going forward, the plan is to include breadcrumbs just below the header on sub-pages of the site. This breadcrumb section will be full-width, and will be able to expand down to show a category navigation panel. This will push any other body content down. If necessary, we can create mockups of how we envision this to look, so that the design can account for it.

```html
<!DOCTYPE html>
<html lang="en">
<head>
<meta charset="utf-8">
<title>Sky Ledger – Home</title>
<link href="https://fonts.googleapis.com/css2?family=Roboto:wght@300;400;500;700&family=Open+Sans:wght@400;600&family=Courier+Prime&display=swap" rel="stylesheet">
<style>
:root{
  --red:#e8352a;
  --red-dark:#b3100f;
  --ink:#333;
  --muted:#777;
  --line:#e6e6e6;
  --orange:#e39b1c;
  --blue:#3a4aa8;
  --foot:#2a2a2a;
  --foot-bottom:#222;
  --foot-text:#bbb;
}
*{box-sizing:border-box;margin:0;padding:0}
html,body{width:726px;height:1200px;overflow:hidden;background:#fff}
body{position:relative;font-family:"Roboto",sans-serif;color:var(--ink)}
.abs{position:absolute}
/* header */
.site-header{position:absolute;left:0;top:0;width:726px;height:64px;border-top:2px solid var(--red);border-bottom:1px solid var(--line)}
.brand-name{position:absolute;left:104px;top:22px;font-family:"Courier Prime",monospace;font-size:16px;color:var(--red)}
.main-nav{position:absolute;left:329px;top:24px;display:flex;font-size:9px}
.main-nav a{color:#333;text-decoration:none;padding:0 12px;border-right:1px solid var(--line);line-height:20px}
.main-nav a:last-child{border-right:none}
.cart{position:absolute;left:568px;top:25px;display:flex;align-items:center;gap:8px;font-size:9px}
.cart-icon{width:19px;height:19px;border:1px solid var(--red);border-radius:50%;display:flex;align-items:center;justify-content:center}
/* hero */
.hero{position:absolute;left:0;top:64px;width:726px;height:336px;background:linear-gradient(180deg,#8c929a 0%,#a9aeb3 40%,#8a8a80 62%,#b9b4a8 100%)}
.hero-title{position:absolute;left:0;width:726px;text-align:center;color:#fff;text-shadow:0 1px 3px rgba(0,0,0,.4)}
.hero-title.line1{top:108px;font-size:25px;font-weight:500}
.hero-title.line2{top:142px;font-family:"Courier Prime",monospace;font-size:27px;letter-spacing:1px}
.quote-btn{position:absolute;left:305px;top:182px;width:116px;height:26px;background:var(--red-dark);color:#fff;font-size:9.5px;font-weight:500;display:flex;align-items:center;justify-content:center;border-radius:2px}
.slide-arrow{position:absolute;top:136px;width:22px;height:22px;border-radius:50%;background:rgba(255,255,255,.25)}
/* spotlight row */
.spotlight-band{position:absolute;left:0;top:400px;width:726px;height:188px;background:linear-gradient(#fff,#f6f6f6);border-bottom:1px solid var(--line)}
.card{position:absolute;top:24px;height:122px;border:1px solid var(--line);background:#fff}
.card-photo{left:104px;width:165px}
.card-photo .ph{position:absolute;left:10px;top:10px;right:10px;bottom:10px;background:linear-gradient(160deg,#f2ede0,#d9d3c4)}
.card-promo{left:280px;width:165px;background:var(--red);border:none}
.promo-thumb{position:absolute;left:14px;top:18px;width:54px;height:54px;border-radius:50%;border:3px solid #fff;background:#a77a35}
.promo-text{position:absolute;left:76px;top:30px;color:#fff;font-size:9.5px;line-height:15px}
.promo-link{position:absolute;left:0;top:103px;width:165px;text-align:center;font-size:9px;color:var(--red);text-decoration:underline}
.card-calibres{left:457px;width:165px}
.calibres{width:100%;height:100%;border-collapse:collapse;font-size:7.2px}
.calibres td{border:1px solid var(--line);padding-left:9px}
.calibres td:nth-child(1){color:var(--orange);width:61px}
.calibres td:nth-child(2){color:var(--blue);width:53px}
.calibres td:nth-child(3){color:#222}
.caption{position:absolute;top:156px;font-size:10px}
.caption em{font-style:normal;color:var(--red)}
/* feature */
.feature-photo{position:absolute;left:104px;top:619px;width:208px;height:166px;border:1px solid var(--line);padding:3px;background:#fff}
.feature-photo div{width:100%;height:100%;background:linear-gradient(160deg,#6a6a6a,#3c3c3c 55%,#8a8a8a)}
.feature-copy{position:absolute;left:333px;top:612px;width:286px}
.feature-copy h2{font-weight:300;font-size:12.8px;line-height:19px;color:#444;margin-bottom:12px}
.feature-copy p{font-family:"Open Sans",sans-serif;font-size:6.4px;line-height:13px;color:#666;margin-bottom:8px}
.dark-btn{display:inline-block;margin-top:2px;background:#222;color:#fff;font-size:7.5px;padding:6px 10px;border-radius:2px}
/* news */
.news-head{position:absolute;left:104px;top:810px;font-size:12.5px;font-weight:400;color:#334}
.news-nav{position:absolute;top:813px;width:12px;height:12px;border:1px solid #ddd;border-radius:50%;font-size:7px;display:flex;align-items:center;justify-content:center;color:#666}
.news-rule{position:absolute;left:104px;top:837px;width:518px;border-top:1px solid var(--line)}
.news-item{position:absolute;top:856px;width:262px}
.news-img{position:absolute;left:0;top:0;width:106px;height:100px}
.news-body{position:absolute;left:119px;top:0;width:137px}
.news-body h3{font-weight:400;font-size:9px;color:#333}
.news-date{font-size:7px;color:var(--red);margin:8px 0 9px}
.news-body p{font-family:"Open Sans",sans-serif;font-size:5.8px;line-height:12.5px;color:#777;text-align:justify}
.news-more{font-family:"Open Sans",sans-serif;font-size:6.2px;color:#666;margin-top:8px}
/* brands */
.brands{position:absolute;left:0;top:984px;width:726px;height:58px;background:#f7f7f7;border-top:1px solid var(--line)}
.brands-label{position:absolute;left:105px;top:14px;font-size:9px;line-height:16px;border-right:1px solid var(--line);padding-right:14px}
.brand{position:absolute;top:20px;font-size:14px;font-weight:700}
/* footer */
.site-footer{position:absolute;left:0;top:1042px;width:726px;height:158px;background:var(--foot)}
.foot-col{position:absolute;top:20px;color:var(--foot-text)}
.foot-col h4{font-weight:400;font-size:9px;color:#ddd;margin-bottom:10px}
.foot-col li{list-style:none;font-family:"Open Sans",sans-serif;font-size:6.4px;line-height:14px}
.foot-col p{font-family:"Open Sans",sans-serif;font-size:6.6px;line-height:13px}
.sub-input{position:absolute;left:0;top:58px;width:92px;height:19px;background:#333;border:1px solid #3d3d3d;font-size:6px;color:#888;padding:5px 8px;font-family:"Open Sans",sans-serif}
.sub-btn{position:absolute;left:92px;top:58px;width:47px;height:19px;background:var(--red);color:#fff;font-size:7.5px;display:flex;align-items:center;justify-content:center;border-radius:2px}
.foot-bottom{position:absolute;left:0;top:118px;width:726px;height:40px;background:var(--foot-bottom);text-align:center;font-family:"Open Sans",sans-serif;font-size:6.5px;color:#bbb;line-height:24px}
.foot-bottom b{font-weight:400;color:var(--orange)}
</style>
</head>
<body>

<header class="site-header">
  <div class="brand-name">Sky Ledger</div>
  <nav class="main-nav"><a>HOME</a><a>ABOUT US</a><a>SERVICES</a><a>CONTACT</a></nav>
  <div class="cart">
    <span class="cart-icon"><svg width="9" height="8" viewBox="0 0 9 8"><path d="M0 1h1.5l1 4.5h5L8.5 2H2" fill="none" stroke="#e8352a" stroke-width="1"/><circle cx="3" cy="7" r=".8" fill="#e8352a"/><circle cx="7" cy="7" r=".8" fill="#e8352a"/></svg></span>
    <span>0 items</span>
  </div>
</header>

<section class="hero" role="img" aria-label="Gunship aircraft parked on an airfield apron under a grey sky">
  <div class="slide-arrow" style="left:19px"><svg width="22" height="22"><path d="M13 6l-5 5 5 5" stroke="#fff" stroke-width="1.5" fill="none"/></svg></div>
  <div class="slide-arrow" style="left:682px"><svg width="22" height="22"><path d="M9 6l5 5-5 5" stroke="#fff" stroke-width="1.5" fill="none"/></svg></div>
  <h1 class="hero-title line1">When You Need Backup, Just Call</h1>
  <div class="hero-title line2">Sky Ledger</div>
  <a class="quote-btn">REQUEST A QUOTE</a>
</section>

<section class="spotlight-band">
  <div class="card card-photo"><div class="ph" role="img" aria-label="Product photo of three sorting bowls filled with brass cases"></div></div>
  <div class="card card-promo">
    <div class="promo-thumb" role="img" aria-label="Pile of brass cartridge cases"></div>
    <div class="promo-text">The Brass Tidy 3<br>Bowl Setwith .380<br>Brass Tidy Plate</div>
    <svg class="abs" style="left:0;top:88px" width="165" height="34" viewBox="0 0 165 34"><path d="M0 34 Q82 -14 165 34 Z" fill="#fff"/></svg>
    <div class="promo-link">HOW TO BUY</div>
  </div>
  <div class="card card-calibres">
    <table class="calibres">
      <tr><td>.45 ACP</td><td>.40 S&amp;W</td><td>9mmP</td></tr>
      <tr><td>.44 Mag</td><td>10mm Auto</td><td>.380 ACP</td></tr>
      <tr><td>.308 Win</td><td>.357 Mag</td><td>.38 Super</td></tr>
      <tr><td>7.62x39mm</td><td>.38 Special</td><td>.223 Rem</td></tr>
    </table>
  </div>
  <div class="caption" style="left:104px">Introducing The <em>Brass</em> Tidy</div>
  <div class="caption" style="left:280px"><em>R941</em> COD or EFT</div>
  <div class="caption" style="left:469px;color:var(--orange)">Yellow</div>
  <div class="caption" style="left:538px;color:var(--blue)">Blue</div>
  <div class="caption" style="left:587px">Black</div>
</section>

<div class="feature-photo"><div role="img" aria-label="Two soldiers in helmets holding rifles beside a concrete wall"></div></div>
<section class="feature-copy">
  <h2>Separate your mixed cases faster than ever before with the Brass Tidy</h2>
  <p>Available for the first time in South Africa, the Brass Tidy system is comprised of several levels, with each designed to filter a specific calibre. Working over a bucket, simply shake mixed cases through each level and your brass will be separated in no time at all.</p>
  <p>The basic Brass Tidy set of three bowls handles the most common calibres. Give the yellow pan a few quick shakes, and everything smaller than .45 ACP falls through to the blue pan, which is calibrated for .40 S&amp;W. A few more shakes, and the black pan is set to take care of 9mm cases. One last round, and everything smaller</p>
  <a class="dark-btn">READ MORE</a>
</section>

<h2 class="news-head">LATEST NEWS</h2>
<div class="news-nav" style="left:596px">‹</div>
<div class="news-nav" style="left:611px">›</div>
<div class="news-rule"></div>

<article class="news-item" style="left:104px">
  <div class="news-img" role="img" aria-label="Soldiers in desert gear on rocky ground under blue sky" style="background:linear-gradient(180deg,#5d86bf,#9db6d6 55%,#c9c2b0)"></div>
  <div class="news-body">
    <h3>Lorem ipsum dolor sit amet</h3>
    <div class="news-date">Jan 08, 2015</div>
    <p>Lorem ipsum dolor sit amet, consectetuer adipiscing elit, sed diam nonummy nibh euismod tincidunt ut laoreet dolore Lorem ipsum dolor sit amet, consectetuer</p>
    <div class="news-more">Read More +</div>
  </div>
</article>
<article class="news-item" style="left:373px">
  <div class="news-img" role="img" aria-label="Gunship aircraft flying against a pale blue sky" style="background:linear-gradient(180deg,#7f98b8,#b7c6d8)"></div>
  <div class="news-body">
    <h3>Lorem ipsum dolor sit amet</h3>
    <div class="news-date">Jan 08, 2015</div>
    <p>Lorem ipsum dolor sit amet, consectetuer adipiscing elit, sed diam nonummy nibh euismod tincidunt ut laoreet dolore Lorem ipsum dolor sit amet, consectetuer</p>
    <div class="news-more">Read More +</div>
  </div>
</article>

<section class="brands">
  <div class="brands-label">BRANDS<br>IN STOCK</div>
  <div class="brand" style="left:176px;color:#222">Ridgeholt</div>
  <div class="brand" style="left:294px;color:#c8261f">Marlowe</div>
  <div class="brand" style="left:406px;color:#555;font-weight:400;font-size:15px">KV Werk</div>
  <div class="brand" style="left:520px;color:#c8261f;font-size:12px;top:22px">Castellan Arms</div>
</section>

<footer class="site-footer">
  <div class="foot-col" style="left:104px">
    <h4>CONTACT INFO</h4>
    <p>48 Kestrel Lane,<br>Midrand North</p>
    <p style="margin-top:6px">
      <svg width="6" height="7"><rect x="1" y="0" width="4" height="7" rx="1" fill="none" stroke="#bbb"/></svg>&nbsp; +27 010 555 0148<br>
      <svg width="8" height="6"><rect x=".5" y=".5" width="7" height="5" fill="none" stroke="#bbb"/><path d="M.5 .5l3.5 3 3.5-3" fill="none" stroke="#bbb"/></svg>&nbsp; info@skyledger.co.za
    </p>
  </div>
  <div class="foot-col" style="left:229px"><h4>MY ACCOUNT</h4><ul><li>Track Order</li><li>Order History</li><li>Preferences</li></ul></div>
  <div class="foot-col" style="left:312px"><h4>SKY LEDGER</h4><ul><li>Track Order</li><li>Order History</li><li>Preferences</li></ul></div>
  <div class="foot-col" style="left:395px"><h4>HELP</h4><ul><li>Shipping Options</li><li>Payment Options</li><li>FAQ</li></ul></div>
  <div class="foot-col" style="left:483px;width:145px;height:90px">
    <h4>NEWSLETTER SIGNUP</h4>
    <p>Sign up to Our Newsletter &amp; get attractive Offers by subscribing to our newsletters.</p>
    <div class="sub-input">Enter Your Email</div>
    <div class="sub-btn">subscribe</div>
  </div>
  <div class="foot-bottom">©2013 - 2014 <b>SKY LEDGER</b>, All Rights Reserved.</div>
</footer>

</body>
</html>
```